Maplecrest Disability - Social Security Disability Attorneys

Our company is expanding to attract clients nationwide for our social security disability practice. We have a logo, but I am looking for a creative and elegant letterhead that projects an image of being technologically advanced but still professional enough for the legal field. I am looking for the "wow factor" combined with this is still professional enough for a law practice.

Requesting letterhead and business card design
Updates

Had to update and change the logo. The previous logo had a typo. Please send updates with the new logo for consideration. The letterhead and business cards should be professional enough to be used for a law firm. Thanks.

Industry/Entity Type

Law Practice, Law Firm, Healthcare Industry, Government

Colors

Designer to choose colors to be used in the design.

Requirements
Nice to have
• **Please create a vertical design for the business card**

```html
<!DOCTYPE html>
<html lang="en">
<head>
<meta charset="utf-8">
<title>Maplecrest Disability – Stationery</title>
<link href="https://fonts.googleapis.com/css2?family=Lato:wght@400;700&family=Roboto:wght@400;700&family=Great+Vibes&display=swap" rel="stylesheet">
<style>
  :root{
    --backdrop:#bfbfc1;
    --paper:#ffffff;
    --ink:#222428;
    --brand-blue:#3f5fc8;
    --band-blue:#4167d6;
    --card-blue:#5670bb;
    --brand-orange:#f07f22;
  }
  *{box-sizing:border-box;margin:0;padding:0}
  html,body{width:1200px;height:848px;overflow:hidden;background:var(--backdrop)}
  body{position:relative;font-family:"Lato",sans-serif;color:var(--ink)}

  /* ---------- Letterhead ---------- */
  .letterhead{position:absolute;left:151px;top:118px;width:455px;height:623px;background:var(--paper);overflow:hidden}
  .brand{position:absolute;text-align:center;font-family:"Lato",sans-serif;color:var(--brand-blue)}
  .brand-dot{display:block;margin:0 auto 5px;border-radius:50%;background:var(--brand-orange)}
  .brand-name{display:block;text-transform:uppercase;letter-spacing:.08em;font-weight:400;white-space:nowrap}
  .brand-tag{display:block;text-transform:uppercase;font-weight:400;white-space:nowrap}

  .letterhead .brand{left:25px;top:36px;width:140px}
  .letterhead .brand-dot{width:8px;height:8px}
  .letterhead .brand-name{font-size:11px}
  .letterhead .brand-tag{font-size:3.6px;letter-spacing:.16em;margin-top:2px}

  .lh-contact{position:absolute;left:321px;top:36px;padding-left:7px;border-left:1px solid var(--brand-orange);font-size:7px;line-height:10.4px;font-family:"Roboto",sans-serif;font-style:normal}
  .lh-contact .row{display:flex;align-items:center;gap:5px}
  .lh-contact svg{width:7px;height:7px;flex:none}
  .lh-contact .addr{margin-bottom:2px}

  .letter{position:absolute;left:25px;top:149px;width:406px;font-size:8.9px;line-height:9.9px}
  .letter .date{margin-bottom:11px}
  .letter .block{margin-bottom:11px}
  .letter .salutation{font-weight:700;font-size:10.8px;margin:5px 0 12px}
  .letter p.body{text-align:justify;margin-bottom:10px}
  .letter .closing{margin-top:21px}
  .letter .signature{font-family:"Great Vibes",cursive;font-size:22px;margin-top:9px;line-height:26px}

  .lh-footer{position:absolute;left:0;right:0;bottom:0;height:30px}
  .lh-footer .rule{position:absolute;left:0;right:0;top:0;height:4px;background:var(--brand-orange)}
  .lh-footer .band{position:absolute;left:0;right:0;top:8px;bottom:0;background:var(--band-blue)}

  /* ---------- Business cards ---------- */
  .card{position:absolute;top:234px;width:213px;height:373px;overflow:hidden;font-family:"Roboto",sans-serif;text-align:center}
  .card-front{left:627px;background:var(--paper);color:var(--ink)}
  .card-back{left:864px;background:var(--card-blue);color:#fff}

  .card .brand{left:0;width:100%}
  .card-front .brand{top:44px}
  .card-back .brand{top:150px;color:#fff}
  .card .brand-dot{width:8px;height:8px}
  .card .brand-name{font-size:12.5px}
  .card .brand-tag{font-size:3.8px;letter-spacing:.16em;margin-top:2px}

  .person{position:absolute;top:131px;width:100%}
  .person-name{color:var(--brand-orange);font-weight:700;font-size:12.5px;letter-spacing:.01em}
  .person-role{display:flex;align-items:center;justify-content:center;gap:3px;font-size:9.5px;margin-top:2px}
  .person-role::before,.person-role::after{content:"";width:28px;height:1px;background:var(--brand-orange)}

  .card-addr{position:absolute;top:191px;width:100%;font-size:8.6px;line-height:12.4px}
  .icon-pill{position:absolute;top:228px;left:70px;width:73px;height:19px;border-radius:3px;background:var(--brand-orange);display:flex;align-items:center;justify-content:space-evenly}
  .icon-pill svg{width:10px;height:10px}
  .card-contact{position:absolute;top:258px;width:100%;font-size:8.6px;line-height:14px}
  .card-footer{position:absolute;left:0;right:0;bottom:0;height:16px}
  .card-footer .rule{position:absolute;left:0;right:0;top:0;height:3px;background:var(--brand-orange)}
  .card-footer .band{position:absolute;left:0;right:0;top:5px;bottom:0;background:var(--card-blue)}

  .sectors{position:absolute;top:268px;width:100%;font-size:8.6px;line-height:12.6px}
</style>
</head>
<body>

<main class="letterhead">
  <div class="brand">
    <span class="brand-dot"></span>
    <span class="brand-name">Maplecrest Disability</span>
    <span class="brand-tag">Social Security Disability Attorneys</span>
  </div>

  <address class="lh-contact">
    <div class="addr">Suite 4, Level 12, Harbour Lane<br>Brookvale NSW 2100</div>
    <div class="row">
      <svg viewBox="0 0 10 10"><path d="M2 1 L4 1 L4.6 3.4 L3.4 4.2 Q4.4 6 5.8 6.6 L6.6 5.4 L9 6 L9 8 Q8.4 9.2 6.6 8.8 Q2 7.4 1 3 Q0.8 1.4 2 1Z" fill="var(--brand-orange)"/></svg>
      <span>555-214-7390</span>
    </div>
    <div class="row">
      <svg viewBox="0 0 10 10"><rect x="0.5" y="2" width="9" height="6.2" fill="var(--brand-orange)"/><path d="M0.5 2 L5 5.6 L9.5 2" stroke="#fff" stroke-width="0.8" fill="none"/></svg>
      <span>info@maplecrestdisability.com</span>
    </div>
    <div class="row">
      <svg viewBox="0 0 10 10"><circle cx="5" cy="5" r="4.5" fill="var(--brand-orange)"/><path d="M1 5 H9 M5 0.5 V9.5" stroke="#fff" stroke-width="0.7"/></svg>
      <span>www.maplecrestdisability.com</span>
    </div>
  </address>

  <article class="letter">
    <div class="date">January-03-2020</div>
    <div class="block">Mr, Daniel Reyes<br>President</div>
    <div class="block">Fenwick Corporation<br>123 Street Name, Suite# 10<br>City, State, 120023</div>
    <div class="salutation">Dear Mr, Daniel</div>
    <p class="body">Lorem ipsum dolor sit amet, consectetur adipisicing elit, sed do eiusmod tempor incididunt ut labore et dolore magna aliqua. Ut enim ad minim veniam, quis nostrud exercitation ullamco laboris nisi ut aliquip ex ea commodo consequat. Duis aute irure dolor in reprehenderit in voluptate velit esse cillum dolore eu fugiat nulla pariatur.</p>
    <p class="body">Lorem ipsum dolor sit amet, consectetur adipisicing elit, sed do eiusmod tempor incididunt ut labore et dolore magna aliqua. Ut enim ad minim veniam, quis nostrud exercitation ullamco laboris nisi ut aliquip ex ea commodo consequat. Duis aute irure dolor in reprehenderit in voluptate velit esse cillum dolore eu fugiat nulla pariatur.</p>
    <p class="body">Lorem ipsum dolor sit amet, consectetur adipisicing elit, sed do eiusmod tempor incididunt ut labore et dolore magna aliqua. Ut enim ad minim veniam, quis nostrud exercitation ullamco laboris nisi ut aliquip ex ea commodo consequat.</p>
    <p class="body">Excepteur sint occaecat cupidatat non proident, sunt in culpa qui officia deserunt mollit anim id est laborum. re et dolore magnam aliquam quaerat voluptatem.</p>
    <div class="closing">Regards</div>
    <div class="signature">Clara Bennett</div>
  </article>

  <div class="lh-footer" aria-hidden="true">
    <div class="rule"></div>
    <div class="band"></div>
  </div>
</main>

<section class="card card-front">
  <div class="brand">
    <span class="brand-dot"></span>
    <span class="brand-name">Maplecrest Disability</span>
    <span class="brand-tag">Social Security Disability Attorneys</span>
  </div>

  <div class="person">
    <div class="person-name">OWEN HARTLEY</div>
    <div class="person-role">Co-Founder</div>
  </div>

  <div class="card-addr">Suite 4, Level 12, Harbour Lane<br>Brookvale NSW 2100</div>

  <div class="icon-pill" aria-hidden="true">
    <svg viewBox="0 0 10 10"><path d="M2 1 L4 1 L4.6 3.4 L3.4 4.2 Q4.4 6 5.8 6.6 L6.6 5.4 L9 6 L9 8 Q8.4 9.2 6.6 8.8 Q2 7.4 1 3 Q0.8 1.4 2 1Z" fill="none" stroke="#fff" stroke-width="0.9"/></svg>
    <svg viewBox="0 0 10 10"><rect x="0.8" y="2.2" width="8.4" height="5.8" fill="none" stroke="#fff" stroke-width="0.9"/><path d="M0.8 2.2 L5 5.6 L9.2 2.2" stroke="#fff" stroke-width="0.9" fill="none"/></svg>
    <svg viewBox="0 0 10 10"><circle cx="5" cy="5" r="4.3" fill="none" stroke="#fff" stroke-width="0.9"/><path d="M0.7 5 H9.3 M5 0.7 V9.3" stroke="#fff" stroke-width="0.8"/></svg>
  </div>

  <div class="card-contact">
    555-214-7390<br>
    info@maplecrestdisability.com<br>
    www.maplecrestdisability.com
  </div>

  <div class="card-footer" aria-hidden="true">
    <div class="rule"></div>
    <div class="band"></div>
  </div>
</section>

<section class="card card-back">
  <div class="brand">
    <span class="brand-dot"></span>
    <span class="brand-name">Maplecrest Disability</span>
    <span class="brand-tag">Social Security Disability Attorneys</span>
  </div>
  <div class="sectors">Law Practice, Law Firm,<br>Healthcare Industry, Government</div>
</section>

</body>
</html>
```